Established research company needs fresh new powerpoint template

We need a powerpoint template for an established research and advisory company called Quenlow Partnership. We develop policy, improve delivery, and build capacity within the public sector - mainly in relation to education and young people.

We have a long and successful track record in our sector, and have a grown-up, clean brand. We already have a logo (see attached) and want a simple, clean powerpoint template that incorporates our logo and colours and matches the brand identity on our website: https://www.quenlowpartnership.com/

We need a title slide, a section header slide, a two-column slide for two panels of text, a two-column slide for one panel of text and one panel of imagery, and a single-column slide for text.

We want a template with built-in Styles so our team can make consistent-looking presentations without any manual formatting. We also want to use a font that will be compatible with devices used across a range of clients.

```html
<!DOCTYPE html>
<html lang="en">
<head>
<meta charset="utf-8">
<title>Quenlow Partnership – Presentation Template</title>
<link rel="stylesheet" href="https://fonts.googleapis.com/css2?family=Poppins:wght@300;400;500;600;800;900&display=swap">
<style>
  :root{
    --canvas:#b1b3b6;
    --orange:#f47a36;
    --slate:#8f99a8;
    --panel:#949dab;
    --ink:#111111;
    --body:#2f2f2f;
    --white:#ffffff;
    --line:#9aa2ae;
  }
  *{box-sizing:border-box;margin:0;padding:0}
  html,body{width:1200px;height:3914px;overflow:hidden}
  body{background:var(--canvas);font-family:"Poppins",Arial,sans-serif;position:relative}
  .slide{position:absolute;left:102px;width:1002px;height:562px;overflow:hidden;background:var(--white)}
  .abs{position:absolute}
  .brand{position:absolute;color:var(--orange);font-weight:600;line-height:.9;font-size:34px;letter-spacing:-.5px}
  .brand span{display:block}

  /* title slide */
  .s-title{top:94px}
  .s-title .photo{inset:0;background:linear-gradient(160deg,#4a4440 0%,#2f2d2b 45%,#1b1f24 100%)}
  .s-title .brand{left:47px;top:48px;font-size:44px}
  .s-title .bar{left:397px;top:45px;width:5px;height:107px;background:var(--orange)}
  .s-title .tagline{left:462px;top:38px;color:var(--white);font-weight:300;font-size:30px;line-height:41px}

  /* section header */
  .s-section{top:725px}
  .s-section .photo{inset:0;background:linear-gradient(120deg,#f1f2f4 0%,#e6e8eb 55%,#dcdfe3 100%)}
  .s-section .rule-top{left:235px;top:178px;width:195px;height:2px;background:var(--orange)}
  .s-section .rule-bottom{left:475px;top:290px;width:289px;height:2px;background:var(--slate)}
  .s-section h1{left:0;width:1002px;top:188px;text-align:center;font-weight:800;font-size:76px;line-height:95px;letter-spacing:-1px;padding-left:4px}
  .s-section h1 .accent{color:var(--orange)}
  .s-section h1 .muted{color:var(--slate)}
  .s-section .brand{left:14px;top:484px}

  /* headings shared */
  .heading{font-weight:800;font-size:23px;color:var(--ink);letter-spacing:-.3px}
  .heading-rule{height:3px;width:62px;background:var(--ink)}

  /* text + image */
  .s-split{top:1353px}
  .s-split .photo{left:0;top:0;width:440px;height:474px;background:linear-gradient(135deg,#efeae4 0%,#d9d2c9 50%,#b9b3ab 100%)}
  .s-split .heading{left:503px;top:66px}
  .s-split .heading-rule{left:503px;top:114px}
  .s-split .copy{left:503px;top:156px;width:420px;font-size:17px;line-height:29px;color:var(--body)}
  .s-split .brand{left:14px;top:484px}

  /* services grid */
  .s-services{top:1984px}
  .s-services .heading{left:27px;top:22px}
  .s-services .heading-rule{left:27px;top:64px}
  .service{position:absolute;width:468px;height:181px;background:var(--panel);color:var(--white)}
  .service .icon{position:absolute;left:28px;top:45px;width:91px;height:91px;border-radius:50%;background:var(--white);display:flex;align-items:center;justify-content:center}
  .service h2{position:absolute;left:138px;top:24px;width:310px;font-size:16.5px;font-weight:800;line-height:21px;letter-spacing:.2px}
  .service p{position:absolute;left:138px;width:310px;font-size:11.5px;line-height:15.5px;font-weight:400}
  .s-services .brand{left:27px;top:484px}

  /* publications */
  .s-pubs{top:2614px}
  .s-pubs .heading{left:27px;top:22px}
  .s-pubs .heading-rule{left:27px;top:64px}
  .pub{position:absolute;top:99px;height:360px;border:1.5px solid var(--line)}
  .pub h2{position:absolute;left:24px;width:420px;font-size:11.5px;font-weight:700;line-height:15.5px;color:var(--ink)}
  .pub p{position:absolute;left:26px;width:420px;font-size:12.3px;line-height:25px;color:var(--body)}
  .s-pubs .brand{left:27px;top:477px}

  /* closing */
  .s-close{top:3244px}
  .s-close .photo{inset:0;background:linear-gradient(170deg,#2b2b2b 0%,#1d1d1d 60%,#151515 100%)}
  .s-close .rule{left:319px;width:364px;height:1.5px;background:#d9d9d9}
  .s-close h1{left:0;width:1002px;top:218px;text-align:center;color:var(--white);font-weight:300;font-size:70px;line-height:88px;letter-spacing:1px}
  .s-close .brand{left:24px;top:446px;font-size:44px}
</style>
</head>
<body>

<section class="slide s-title">
  <div class="abs photo" role="img" aria-label="Dimly lit photograph of a team meeting around a conference table"></div>
  <div class="brand"><span>quenlow</span><span>partnership</span></div>
  <div class="abs bar"></div>
  <p class="abs tagline">We help the public sector<br>solve problems and<br>deliver effectively.</p>
</section>

<section class="slide s-section">
  <div class="abs photo" role="img" aria-label="Faded photograph of colleagues reviewing documents in an office"></div>
  <div class="abs rule-top"></div>
  <h1 class="abs"><span class="accent">WHO</span> <span class="muted">WE ARE</span></h1>
  <div class="abs rule-bottom"></div>
  <div class="brand"><span>quenlow</span><span>partnership</span></div>
</section>

<section class="slide s-split">
  <div class="abs photo" role="img" aria-label="Photograph of two colleagues studying a printed report together"></div>
  <h2 class="abs heading">WHO WE ARE</h2>
  <div class="abs heading-rule"></div>
  <p class="abs copy">We have in-depth experience of working with the public sector, in the UK and overseas, in education, local government, health and social care. We have expertise and a proven track record in developing policy and strategy, solving delivery problems, undertaking national evaluations and writing influential research reports, advising on organisational reform, and facilitating workshops and conferences.</p>
  <div class="brand"><span>quenlow</span><span>partnership</span></div>
</section>

<section class="slide s-services">
  <h2 class="abs heading">WHAT WE DO</h2>
  <div class="abs heading-rule"></div>

  <article class="service" style="left:27px;top:88px">
    <div class="icon"><svg width="44" height="48" viewBox="0 0 44 48" fill="none" stroke="#f47a36" stroke-width="2.5"><rect x="4" y="6" width="36" height="40" rx="2"/><rect x="14" y="2" width="16" height="8" rx="1"/><path d="M11 36l8-9 6 5 9-11"/><circle cx="12" cy="19" r="2"/><path d="M27 38h6"/></svg></div>
    <h2>STRATEGIC PLANNING</h2>
    <p style="top:50px">We can support you to develop policies and strategies and design performance and delivery systems to implement these. We have a strong record in engaging stakeholders in designing systems and strategic planning.</p>
  </article>

  <article class="service" style="left:511px;top:88px">
    <div class="icon"><svg width="48" height="48" viewBox="0 0 48 48" fill="none" stroke="#f47a36" stroke-width="2.5"><path d="M8 8l32 32M40 8L8 40"/><circle cx="24" cy="24" r="7"/><path d="M14 44h20"/></svg></div>
    <h2>DELIVERY, EFFICIENCY AND INNOVATION</h2>
    <p style="top:72px">We can assess and strengthen programme implementation, review progress of established projects, and provide rapid feedback from delivery partners. We can also work with you to reconfigure services and resources to maximise value for money.</p>
  </article>

  <article class="service" style="left:27px;top:288px">
    <div class="icon"><svg width="46" height="48" viewBox="0 0 46 48" fill="none" stroke="#f47a36" stroke-width="2.5"><path d="M6 4h20l8 8v14"/><path d="M6 4v40h18"/><path d="M12 16h14M12 23h10M12 30h8"/><circle cx="32" cy="34" r="7"/><path d="M37 39l6 6"/></svg></div>
    <h2>RESEARCH AND EVALUATION</h2>
    <p style="top:50px">We are skilled in evaluating the impact of policies, using both qualitative and quantitative techniques, and can undertake bespoke research projects to inform policy making and delivery.</p>
  </article>

  <article class="service" style="left:511px;top:288px">
    <div class="icon"><svg width="50" height="48" viewBox="0 0 50 48" fill="none" stroke="#f47a36" stroke-width="2.5"><circle cx="12" cy="9" r="5"/><circle cx="38" cy="9" r="5"/><path d="M4 28v-8a8 8 0 0 1 16 0v8M30 28v-8a8 8 0 0 1 16 0v8"/><path d="M8 28v16M16 28v16M34 28v16M42 28v16"/><path d="M20 24h10"/></svg></div>
    <h2>ORGANISATIONAL CAPACITY</h2>
    <p style="top:50px">We will transfer skills and knowledge in every project we undertake. In addition we can work with you to create dedicated performance and delivery capability within your organization. We coach and train top teams and facilitate partner and stakeholder workshops.</p>
  </article>

  <div class="brand"><span>quenlow</span><span>partnership</span></div>
</section>

<section class="slide s-pubs">
  <h2 class="abs heading">PUBLICATIONS</h2>
  <div class="abs heading-rule"></div>

  <article class="pub" style="left:27px;width:475px">
    <h2 style="top:28px">PRELIMINARY RESEARCH INTO HOW TRUSTS AND SCHOOLS NARROW ATTAINMENT GAPS BETWEEN PUPILS FROM DIFFERENT ETHNIC GROUPS</h2>
    <p style="top:88px">In January 2023, the Ministry for Schools, working with the Central Office's Fairness Unit, commissioned Quenlow Partnership to undertake exploratory research into how academy trusts and schools have improved the achievement of, and closed achievement gaps between, pupils from different ethnic groups. The research took place during the spring term and the first half of the summer term 2023, and involved discussions with trust and school leaders within nine academy trusts, one maintained school and national education sector organisations.</p>
  </article>

  <article class="pub" style="left:519px;width:472px">
    <h2 style="top:36px">FROM HOME TO THE CLASSROOM: MAKING TRAVEL TO SCHOOL SERVICES SUSTAINABLE</h2>
    <p style="top:78px">In 2019, Quenlow Partnership published research that showed the pressures placed on local government finances by duties to transport children and young people to school. Four years later, county councils and county unitary authorities are facing a perfect storm in relation to expenditure on home to school transport. This research, commissioned by the Shire Councils Forum, explores the factors driving increasing expenditure on home to school transport, projects what may happen to budgets in future if no policy changes are made, and makes recommendations for national legislative change.</p>
  </article>

  <div class="brand"><span>quenlow</span><span>partnership</span></div>
</section>

<section class="slide s-close">
  <div class="abs photo" role="img" aria-label="Darkened photograph of a meeting room with people seated at a table"></div>
  <div class="abs rule" style="top:206px"></div>
  <h1 class="abs">Thank You</h1>
  <div class="abs rule" style="top:318px"></div>
  <div class="brand"><span>quenlow</span><span>partnership</span></div>
</section>

</body>
</html>
```